Financial Advisor Resource Firm needs business card design

Need business card design for company in Omaha NE called Meridale Circle. We provide resources to financial advisors....workshop programs, retirement analysis, and insurance planning. I would like to see designs that use grays, greens, black, and white colors. The final design should communicate 'collaboration' and be simple yet attractive to financial planning clients. I will attached our logo and another picture of a puzzle piece coming together. I would like the incorporate the puzzle picture somehow, maybe on the back somehow, with color or just the gray scale....OR, the picture be the front of the card with 'Meridale' definition on it (see upload) and then company logo, employee name, title, address on the back (see ppt uploaded). The following disclosure needs to be included somewhere- Advisory services offered through Stonebrook Assets, LLC.
Updates

I uploaded a svg and ai file of the logo

Target Market(s)

Financial planning clients and financial advisors....so pretty diverse age range of about 40-70.

Industry/Entity Type

Financial Planning

Contact Information for Business Card

Tobias L. Fenwright, MBA
Founder/President
5287 E. Larkin Road
Suite 230
Omaha, NE 68190
Phone- (402) 555-0147
Cell- (402) 555-0183
Fax- (402) 555-0129
email- tobias@meridaleplan.example
web address- www.meridaleplan.example

Colors
1b1b1b
474747
d3d3d3
ffffff
9bcb3c
abd036

Requirements
Must have
• Must include logo provided, must be 2 sided, and must have disclosure...all of these items listed in project description

```html
<!DOCTYPE html>
<html lang="en">
<head>
<meta charset="UTF-8">
<title>Meridale Circle — Business Card</title>
<link href="https://fonts.googleapis.com/css2?family=Poppins:wght@400;500;600&display=swap" rel="stylesheet">
<style>
  :root {
    --ink: #1b1b1b;
    --graphite: #2b2b2b;
    --slate: #474747;
    --mist: #d3d3d3;
    --paper: #ffffff;
    --leaf: #9bcb3c;
    --lime: #abd036;
    --backdrop: #ececec;
  }
  * { box-sizing: border-box; margin: 0; padding: 0; }
  html, body { width: 1200px; height: 920px; overflow: hidden; }
  body {
    background: var(--backdrop);
    font-family: "Poppins", sans-serif;
    position: relative;
  }
  .card {
    position: absolute;
    top: 310px;
    width: 540px;
    height: 300px;
    box-shadow: 0 6px 18px rgba(0,0,0,0.18);
    overflow: hidden;
  }
  .card-front { left: 40px; background: var(--paper); }
  .card-back { left: 620px; background: var(--graphite); }

  .brand {
    position: absolute;
    display: flex;
    align-items: center;
    gap: 8px;
    font-weight: 600;
    letter-spacing: 1px;
    text-transform: uppercase;
    white-space: nowrap;
  }
  .brand-dot {
    width: 14px; height: 14px;
    border-radius: 50%;
    background: var(--leaf);
    flex: none;
  }
  .card-front .brand {
    left: 24px; top: 136px;
    font-size: 20px;
    color: var(--ink);
  }
  .card-back .brand {
    left: 0; right: 0; top: 132px;
    justify-content: center;
    font-size: 31px;
    color: var(--paper);
  }
  .card-back .brand-dot { width: 20px; height: 20px; }

  .divider {
    position: absolute;
    left: 272px; top: 78px;
    width: 2px; height: 146px;
    background: var(--leaf);
  }
  .contact {
    position: absolute;
    left: 288px; top: 72px;
    color: var(--slate);
  }
  .contact-name {
    font-size: 17px;
    font-weight: 500;
    color: var(--leaf);
    letter-spacing: 0.3px;
    text-transform: uppercase;
    line-height: 24px;
  }
  .contact-title {
    font-size: 12px;
    line-height: 18px;
    margin-bottom: 12px;
    color: var(--slate);
  }
  .contact-list { list-style: none; }
  .contact-list li {
    display: flex;
    align-items: center;
    gap: 9px;
    font-size: 13px;
    line-height: 19px;
    white-space: nowrap;
  }
  .icon { width: 10px; height: 10px; flex: none; }
  .accent { color: var(--leaf); }

  .address-band {
    position: absolute;
    left: 0; right: 0; top: 253px;
    height: 29px;
    background: var(--graphite);
    color: var(--paper);
    font-size: 12.5px;
    display: flex;
    align-items: center;
    justify-content: center;
    gap: 7px;
  }
  .address-band .icon { width: 10px; height: 13px; }

  .disclosure {
    position: absolute;
    left: 0; right: 0; top: 284px;
    text-align: center;
    font-size: 8.5px;
    line-height: 14px;
    color: var(--slate);
  }

  .back-url {
    position: absolute;
    left: 0; right: 0; top: 256px;
    text-align: center;
    color: var(--mist);
    font-size: 12.5px;
    letter-spacing: 1px;
  }
</style>
</head>
<body>

<section class="card card-front">
  <div class="brand"><span class="brand-dot"></span>Meridale Circle</div>
  <div class="divider"></div>

  <div class="contact">
    <h1 class="contact-name">Tobias L. Fenwright, MBA</h1>
    <p class="contact-title">Founder / President</p>
    <ul class="contact-list">
      <li>
        <svg class="icon" viewBox="0 0 10 10"><path fill="#9bcb3c" d="M2 0.5 L3.6 2.6 2.8 3.6 Q4 5.8 6.4 7.2 L7.4 6.4 9.5 8 8.4 9.5 Q4.5 9.4 0.5 1.6 Z"/></svg>
        <span>(402) 555-0147</span>
      </li>
      <li>
        <svg class="icon" viewBox="0 0 10 10"><rect x="2.5" y="0.5" width="5" height="9" rx="1" fill="none" stroke="#9bcb3c" stroke-width="1.2"/></svg>
        <span>(402) 555-0183</span>
      </li>
      <li>
        <svg class="icon" viewBox="0 0 10 10"><rect x="2.5" y="0.5" width="5" height="3" fill="#9bcb3c"/><rect x="0.5" y="3.5" width="9" height="4" rx="0.8" fill="#9bcb3c"/><rect x="2.5" y="6.5" width="5" height="3" fill="#fff" stroke="#9bcb3c" stroke-width="1"/></svg>
        <span>(402) 555-0129</span>
      </li>
      <li>
        <svg class="icon" viewBox="0 0 10 10"><rect x="0.6" y="1.8" width="8.8" height="6.4" fill="none" stroke="#9bcb3c" stroke-width="1"/><path d="M0.6 1.8 L5 5.4 9.4 1.8" fill="none" stroke="#9bcb3c" stroke-width="1"/></svg>
        <span>tobias@meridaleplan.example</span>
      </li>
      <li>
        <svg class="icon" viewBox="0 0 10 10"><circle cx="5" cy="5" r="4.4" fill="none" stroke="#9bcb3c" stroke-width="1"/><ellipse cx="5" cy="5" rx="1.9" ry="4.4" fill="none" stroke="#9bcb3c" stroke-width="0.9"/><path d="M0.6 5 H9.4" stroke="#9bcb3c" stroke-width="0.9"/></svg>
        <span>www.<span class="accent">meridaleplan</span>.example</span>
      </li>
    </ul>
  </div>

  <div class="address-band">
    <svg class="icon" viewBox="0 0 10 13"><path fill="#9bcb3c" d="M5 0.5 A4.3 4.3 0 0 1 9.3 4.8 C9.3 8 5 12.5 5 12.5 C5 12.5 0.7 8 0.7 4.8 A4.3 4.3 0 0 1 5 0.5 Z"/><circle cx="5" cy="4.8" r="1.6" fill="#2b2b2b"/></svg>
    <span>5287 E. Larkin Road Suite 230</span>
  </div>

  <p class="disclosure">Advisory services offered through Stonebrook Assets, LLC.</p>
</section>

<section class="card card-back">
  <div class="brand"><span class="brand-dot"></span>Meridale Circle</div>
  <p class="back-url">www.<span class="accent">meridaleplan</span>.example</p>
</section>

</body>
</html>
```